Company Mission & Values Poster

I'd like an A2 Portrait Poster displaying our company's Mission & Values.
See our website for our logo, fonts, mission & values.
https://valdintor.com.au/

Our Mission: Creating homes for abundant life
Values: Love, Thinking, Team, Zoe.

Some ideas to consider:
Mission as the Headline then
A logo for each of the 4 Values and the words

Target Market(s)

Myself & my team

Industry/Entity Type

Real Estate

Font styles to use
Other font styles liked:
• Company fonts as seen on our website

```html
<!DOCTYPE html>
<html lang="en">
<head>
<meta charset="utf-8">
<title>Valdintor – Our Mission &amp; Values</title>
<link rel="stylesheet" href="https://fonts.googleapis.com/css2?family=Cinzel:wght@700;800;900&family=Poppins:wght@400;500&display=swap">
<style>
  :root {
    --forest: #06392f;
    --forest-deep: #05352b;
    --sage: #8fc48a;
    --sage-text: #7aae73;
    --mint: #e6f4e3;
    --mint-light: #f3faf2;
    --white: #ffffff;
    --ink: #111111;
    --backdrop: #4d4d4d;
    --rule: #cfcfcf;
    --target-red: #d9262a;
    --target-red-soft: #e86a6c;
  }
  * { margin: 0; padding: 0; box-sizing: border-box; }
  html, body { width: 1200px; height: 2260px; overflow: hidden; }
  body { background: var(--backdrop); position: relative; font-family: "Poppins", sans-serif; }

  .poster {
    position: absolute; left: 40px; top: 340px;
    width: 1120px; height: 1580px;
    background: linear-gradient(180deg, var(--mint-light) 25%, var(--mint) 100%);
    box-shadow: 0 20px 40px rgba(0,0,0,.35);
    overflow: hidden;
  }

  /* Header */
  .header { position: absolute; left: 0; top: 0; width: 100%; height: 268px; background: var(--white); }
  .brand { position: absolute; left: 66px; top: 112px; display: flex; align-items: center; gap: 18px; }
  .brand-dot { width: 56px; height: 56px; border-radius: 50%; background: var(--forest); }
  .brand-name { font-family: "Cinzel", serif; font-weight: 700; font-size: 58px; letter-spacing: 6px; color: var(--forest); line-height: 1; }
  .header-rule { position: absolute; left: 591px; top: 80px; width: 2px; height: 160px; background: var(--rule); }
  .target-art { position: absolute; left: 637px; top: 38px; width: 140px; height: 136px; border-radius: 14px;
    background: linear-gradient(135deg, var(--target-red-soft), var(--target-red)); }
  .mission-title { position: absolute; left: 651px; top: 92px; font-family: "Cinzel", serif; font-weight: 900;
    line-height: 80px; font-size: 74px; letter-spacing: -1px; white-space: nowrap; }
  .mission-title .our { display: block; margin-left: 137px; color: var(--forest); }
  .mission-title .mission { display: block; color: var(--sage-text); }

  /* Headline band */
  .headline { position: absolute; left: 0; top: 268px; width: 100%; height: 155px; background: var(--forest-deep);
    text-align: center; font-family: "Cinzel", serif; font-weight: 800; font-size: 60px; line-height: 68px; padding-top: 8px; }
  .headline .lead { color: var(--sage); display: block; }
  .headline .main { color: var(--white); display: block; }

  .intro { position: absolute; left: 60px; top: 452px; width: 1000px; text-align: center;
    font-size: 29px; line-height: 34px; color: var(--ink); }

  /* Value cards */
  .value-card { position: absolute; width: 453px; background: var(--white); border-radius: 44px;
    box-shadow: 0 6px 18px rgba(6,57,47,.12); color: var(--ink); font-size: 22px; line-height: 27px; }
  .value-card h2 { font-family: "Cinzel", serif; font-weight: 800; font-size: 40px; color: var(--forest); line-height: 1; margin-bottom: 12px; }
  .value-card p span { display: block; }
  .card-team { left: 65px; top: 650px; height: 350px; padding: 58px 0 0 40px; }
  .card-team h2 { margin-left: 142px; }
  .card-love { left: 600px; top: 650px; height: 350px; padding: 60px 0 0 46px; }
  .card-zoe { left: 65px; top: 1096px; height: 355px; padding: 80px 0 0 32px; }
  .card-thinking { left: 600px; top: 1096px; height: 355px; padding: 80px 0 0 38px; }
  .card-thinking h2 { margin-left: 170px; }

  .value-icon { position: absolute; width: 110px; height: 110px; border-radius: 50%; border: 5px solid var(--white);
    display: flex; align-items: center; justify-content: center; box-shadow: 0 4px 10px rgba(0,0,0,.12); }
  .value-icon.sage { background: var(--sage); }
  .value-icon.forest { background: var(--forest); }
  .icon-team { left: 48px; top: 626px; }
  .icon-love { left: 948px; top: 626px; }
  .icon-zoe { left: 55px; top: 1055px; }
  .icon-thinking { left: 955px; top: 1055px; }

  /* Values ring */
  .values-ring { position: absolute; left: 318px; top: 808px; width: 480px; height: 480px; }
  .values-core { position: absolute; left: 400px; top: 890px; width: 316px; height: 316px; border-radius: 50%;
    background: var(--white); box-shadow: 0 0 0 8px #eef2ee, 0 6px 18px rgba(0,0,0,.15);
    display: flex; flex-direction: column; align-items: center; justify-content: center;
    font-family: "Cinzel", serif; font-weight: 900; font-size: 68px; line-height: 62px; }
  .values-core .our { color: var(--forest); }
  .values-core .values { color: var(--forest-deep); }
</style>
</head>
<body>
<main class="poster">
  <header class="header">
    <div class="brand">
      <span class="brand-dot"></span>
      <span class="brand-name">VALDINTOR</span>
    </div>
    <div class="header-rule"></div>
    <div class="target-art" role="img" aria-label="Illustration of a red and white target with darts"></div>
    <h1 class="mission-title"><span class="our">OUR</span><span class="mission">MISSION</span></h1>
  </header>

  <section class="headline">
    <span class="lead">CREATING HOMES FOR</span>
    <span class="main">ABUNDANT LIFE</span>
  </section>

  <p class="intro">We wholeheartedly believe that home is an extraordinary place: a haven where life unfolds in all its glory. Where we find solace, make cherished memories with loved ones, and savour the&nbsp; natural beauty that surrounds us.</p>

  <article class="value-card card-team">
    <h2>TEAM</h2>
    <p><span>Property development is a team</span><span>sport. We surround ourselves</span><span>with the best designers and</span><span>advisers. We strive to</span><span>create an environment</span><span>that allows them to</span><span>do their best work</span><span>and love doing it.</span></p>
  </article>
  <article class="value-card card-love">
    <h2>LOVE</h2>
    <p><span>Our mission is founded in our</span><span>love and respect for people -</span><span style="padding-left:54px">those we develop for, those</span><span style="padding-left:90px">in our teams and those</span><span style="padding-left:114px">in the communities we</span><span style="padding-left:124px">create and</span><span style="padding-left:140px">operate within.</span></p>
  </article>
  <article class="value-card card-zoe">
    <h2>ZOE</h2>
    <p><span>Our mission is to create</span><span>places for ‘Zoe’ - the Greek</span><span>word for abundant life. We do</span><span>this through exquisite design,</span><span>quality construction and</span><span>celebrating nature.</span></p>
  </article>
  <article class="value-card card-thinking">
    <h2>THINKING</h2>
    <p><span style="padding-left:112px">We believe in the power</span><span style="padding-left:52px">of thinking. Our rigorous and</span><span>creative processes create</span><span>beautifully considered solutions</span><span>for our purchasers, the</span><span>communities we develop within</span><span>and the environment.</span></p>
  </article>

  <svg class="values-ring" viewBox="0 0 480 480" aria-hidden="true">
    <g fill="none" stroke-width="68">
      <path d="M41.5 226.1 A199 199 0 0 1 226.1 41.5" stroke="#06392f"/>
      <path d="M253.9 41.5 A199 199 0 0 1 438.5 226.1" stroke="#8fc48a"/>
      <path d="M438.5 253.9 A199 199 0 0 1 253.9 438.5" stroke="#06392f"/>
      <path d="M226.1 438.5 A199 199 0 0 1 41.5 253.9" stroke="#8fc48a"/>
    </g>
  </svg>
  <div class="values-core"><span class="our">OUR</span><span class="values">VALUES</span></div>

  <div class="value-icon sage icon-team">
    <svg width="62" height="50" viewBox="0 0 62 50" aria-hidden="true" fill="#06392f">
      <circle cx="31" cy="12" r="10"/><path d="M15 48c0-12 7-20 16-20s16 8 16 20z"/>
      <circle cx="11" cy="17" r="7"/><path d="M0 44c0-9 5-15 11-15 3 0 5 1 7 3-3 4-5 8-5 12z"/>
      <circle cx="51" cy="17" r="7"/><path d="M62 44c0-9-5-15-11-15-3 0-5 1-7 3 3 4 5 8 5 12z"/>
    </svg>
  </div>
  <div class="value-icon forest icon-love">
    <svg width="60" height="56" viewBox="0 0 60 56" aria-hidden="true" fill="#8fc48a">
      <path d="M34 54C20 44 12 36 12 26c0-7 5-12 11-12 5 0 9 3 11 7 2-4 6-7 11-7 6 0 11 5 11 12 0 10-8 18-22 28z"/>
      <path d="M18 12c-5-4-10-5-13-2-3 4-1 10 6 15" fill="none" stroke="#8fc48a" stroke-width="4"/>
      <circle cx="4" cy="40" r="2"/><circle cx="56" cy="8" r="2"/>
    </svg>
  </div>
  <div class="value-icon forest icon-zoe">
    <svg width="56" height="56" viewBox="0 0 56 56" aria-hidden="true" fill="none" stroke="#8fc48a" stroke-width="5">
      <rect x="6" y="6" width="18" height="18" rx="9"/><rect x="32" y="6" width="18" height="18" rx="9"/>
      <rect x="6" y="32" width="18" height="18" rx="9"/><rect x="32" y="32" width="18" height="18" rx="9"/>
      <path d="M20 20l16 16M36 20L20 36"/>
    </svg>
  </div>
  <div class="value-icon sage icon-thinking">
    <svg width="54" height="60" viewBox="0 0 54 60" aria-hidden="true" fill="#06392f">
      <path d="M27 10c-10 0-17 7-17 16 0 6 3 10 7 13v7h20v-7c4-3 7-7 7-13 0-9-7-16-17-16z"/>
      <rect x="17" y="49" width="20" height="4" rx="2"/><rect x="20" y="55" width="14" height="4" rx="2"/>
      <path d="M27 0v6M6 8l4 4M48 8l-4 4M0 26h5M49 26h5" stroke="#06392f" stroke-width="3"/>
    </svg>
  </div>
</main>
</body>
</html>
```